New Business card design to reflect rebrand

I would like a business card design with a good base colour for our new logo and also a placeholder for a profile pic of the card holder. the design needs to be editable to the point that we can easily change the picture of the person and use that design for printmerlo etc. we are looking at a metalic finish business card so will need a good base colour to bring out the finish.

Target Market(s)

prospective customers

Industry/Entity Type

Business

Contact Information for Business Card

I would like one editable design that we can change the name of the card holder and profile picture. The design need to be in a format that be send to printmerlo etc.

Our address is Fenwick Lodge, Copse Lane, Ashcombe Vale, GU14 3TP Tel no. 01483 556172

Requirements
Must have
• place holder for a profile pic for the card holder. in AI or preferably PSD format

```html
<!DOCTYPE html>
<html lang="en">
<head>
<meta charset="utf-8">
<title>Norvale Facility Support – Business Card</title>
<link rel="stylesheet" href="https://fonts.googleapis.com/css2?family=Roboto:wght@400;500;700&display=swap">
<style>
  :root {
    --backdrop: #1f1f1f;
    --navy: #42566f;
    --orange: #e8690f;
    --white: #ffffff;
    --portrait-light: #a6a6a6;
    --portrait-dark: #939393;
  }
  * { margin: 0; padding: 0; box-sizing: border-box; }
  html, body {
    width: 1200px;
    height: 987px;
    overflow: hidden;
    background: var(--backdrop);
    font-family: "Roboto", Arial, sans-serif;
  }
  .canvas {
    position: relative;
    width: 1200px;
    height: 987px;
  }
  .card {
    position: absolute;
    left: 293px;
    width: 615px;
    height: 351px;
    overflow: hidden;
    box-shadow: 0 4px 10px rgba(0, 0, 0, 0.55);
  }
  .card--front { top: 130px; background: var(--navy); }
  .card--back  { top: 505px; background: var(--white); }

  .portrait {
    position: absolute;
    left: 320px;
    top: 22px;
    width: 295px;
    height: 329px;
  }

  .holder-name {
    position: absolute;
    left: 39px;
    top: 181px;
    font-size: 21px;
    font-weight: 700;
    color: var(--orange);
    letter-spacing: 0.3px;
  }
  .holder-role {
    position: absolute;
    left: 39px;
    top: 212px;
    font-size: 15px;
    font-weight: 400;
    color: var(--white);
  }
  .holder-address {
    position: absolute;
    left: 39px;
    top: 247px;
    font-size: 15px;
    line-height: 22px;
    color: var(--white);
    font-style: normal;
  }
  .holder-phone {
    position: absolute;
    left: 39px;
    top: 296px;
    font-size: 15px;
    color: var(--white);
  }

  .brand {
    position: absolute;
    left: 0;
    right: 0;
    top: 170px;
    text-align: center;
    color: var(--navy);
    font-weight: 500;
  }
  .brand__name {
    display: block;
    font-size: 44px;
    letter-spacing: 4px;
    line-height: 46px;
  }
  .brand__tagline {
    display: block;
    font-size: 19px;
    letter-spacing: 3px;
    line-height: 24px;
  }
  .back-rule {
    position: absolute;
    left: 0;
    width: 100%;
    top: 327px;
    height: 3px;
    background: var(--orange);
  }
  .back-band {
    position: absolute;
    left: 0;
    width: 100%;
    top: 331px;
    height: 20px;
    background: var(--navy);
  }
</style>
</head>
<body>
<main class="canvas">
  <section class="card card--front">
    <svg class="portrait" role="img" aria-label="Profile photo placeholder for the card holder" viewBox="0 0 295 329" preserveAspectRatio="none">
      <defs>
        <linearGradient id="portraitFill" x1="0" y1="0" x2="0" y2="1">
          <stop offset="0" stop-color="#a6a6a6"/>
          <stop offset="1" stop-color="#939393"/>
        </linearGradient>
      </defs>
      <rect x="0" y="0" width="295" height="329" fill="url(#portraitFill)"/>
    </svg>
    <h1 class="holder-name">DANIEL HALE</h1>
    <p class="holder-role">CEO/FOUNDER</p>
    <address class="holder-address">Fenwick Lodge,<br>Copse Lane, Ashcombe Vale, GU14 3TP</address>
    <p class="holder-phone">Tel : 01483 556172</p>
  </section>

  <section class="card card--back">
    <p class="brand">
      <span class="brand__name">NORVALE</span>
      <span class="brand__tagline">FACILITY SUPPORT</span>
    </p>
    <div class="back-rule"></div>
    <div class="back-band"></div>
  </section>
</main>
</body>
</html>
```